1" x 3" label needed for essential oil bottle(s) - new ecommerce company

We need a label designed for 10 ml bottles of essential oils. We are offering 9 different types of essential oil: Lavender, Cedarwood, Eucalyptus, Frankincense, Lemon, Orange, Peppermint, Rosemary, and Tea Tree. The label should have a space for the type of essential oil. The bottles are an amber color (am including a photo) as essential oils are sensitive to light. also am including an AI file of our logo, which we'd like included on the label; the logo file also contains our logo colors, a dark blue and light grey. We'd also like the following on the label: "CAUTION: EYE AND SKIN IRRITANT. Avoid contact with eyes and skin. Wash hands after handling. If eye contact occurs, flush with water for 15 minutes. Not intended for topical or internal use. Contains Essential Oils. KEEP OUT OF REACH OF CHILDREN."
Also "Ingredients: 100% pure essential oil, GC tested."
Also "0.33 fl oz (10 ml)
Finally, we will need to include a sideways bar code on the right side of the label, so need 3/8" of white space on the right of the label.
We'd like the label to be calming, but modern, friendly, and confident.

```html
<!DOCTYPE html>
<html lang="en">
<head>
<meta charset="utf-8">
<title>Solenne Essential Oil Labels</title>
<link href="https://fonts.googleapis.com/css2?family=Nunito+Sans:wght@400;600&family=Cormorant+Garamond:wght@300;400&display=swap" rel="stylesheet">
<style>
  :root {
    --page: #f3f3f3;
    --label-black: #060606;
    --art-grey: #1e1e1e;
    --ink-light: #f2f2f2;
    --ink-soft: #d9d9d9;
    --barcode-white: #ffffff;
    --barcode-edge: #d6d6d6;
    --lavender: #d8c4ee;
    --frankincense: #f7dca2;
    --cedarwood: #d4714f;
    --eucalyptus: #a7c5b4;
    --lemon: #f4ed8e;
    --orange: #e9ae69;
    --peppermint: #cff1e2;
    --rosemary: #9ea493;
    --tea-tree: #b3efb5;
  }
  * { box-sizing: border-box; margin: 0; padding: 0; }
  html, body { width: 1200px; height: 890px; overflow: hidden; }
  body { background: var(--page); position: relative; font-family: "Nunito Sans", sans-serif; }

  .label {
    position: absolute;
    width: 691px;
    height: 230px;
    background: var(--label-black);
    color: var(--ink-light);
    transform-origin: 0 0;
    overflow: hidden;
  }
  .label--small { transform: scale(0.570); }

  .label__art {
    position: absolute;
    left: 250px; top: 0;
    width: 203px; height: 230px;
    background: radial-gradient(ellipse at 45% 55%, var(--art-grey) 0%, var(--label-black) 75%);
  }

  .caution {
    position: absolute;
    left: 6px; top: 4px;
    width: 240px;
    text-align: center;
    font-size: 16.5px;
    line-height: 18.4px;
  }
  .caution__title { font-size: 17.5px; text-decoration: underline; display: block; }
  .caution__head { font-size: 17.5px; letter-spacing: .2px; display: block; }
  .caution__ingredients { font-size: 11.3px; line-height: 18px; display: block; white-space: nowrap; }
  .caution__keep { font-size: 13.4px; line-height: 16px; display: block; white-space: nowrap; }

  .brand {
    position: absolute;
    left: 290px; top: 0;
    width: 150px; height: 230px;
    text-align: center;
  }
  .brand__mark {
    position: absolute; left: 62px; top: 16px;
    width: 26px; height: 26px;
    border: 1.5px solid var(--ink-soft);
    border-radius: 50%;
  }
  .brand__name {
    position: absolute; left: -20px; right: -20px; top: 62px;
    font-family: "Cormorant Garamond", serif;
    font-weight: 400;
    font-size: 17px;
    letter-spacing: 6px;
  }
  .brand__claim {
    position: absolute; left: -20px; right: -20px; top: 108px;
    font-family: "Cormorant Garamond", serif;
    font-weight: 300;
    font-size: 27px;
    line-height: 31px;
    color: var(--ink-soft);
  }
  .brand__tested { position: absolute; left: -20px; right: -20px; top: 180px; font-size: 15px; }
  .brand__volume { position: absolute; left: -20px; right: -20px; top: 201px; font-size: 12.5px; letter-spacing: .5px; }

  .oil-band {
    position: absolute;
    left: 453px; top: 0;
    width: 56px; height: 230px;
    display: flex; align-items: center; justify-content: center;
  }
  .oil-band__name {
    writing-mode: vertical-rl;
    transform: rotate(180deg);
    font-family: "Cormorant Garamond", serif;
    font-weight: 400;
    font-size: 39px;
    color: var(--label-black);
    white-space: nowrap;
  }

  .info {
    position: absolute;
    left: 509px; top: 0;
    width: 96px; height: 230px;
    overflow: hidden;
  }
  .info__turn {
    position: absolute;
    left: 0; top: 230px;
    width: 230px; height: 96px;
    transform: rotate(-90deg);
    transform-origin: 0 0;
    padding: 6px 6px 0 8px;
  }
  .info__social { font-size: 19px; line-height: 24px; white-space: nowrap; }
  .info__address { font-size: 11px; line-height: 13.5px; white-space: nowrap; margin-top: 2px; }

  .barcode-space {
    position: absolute;
    left: 605px; top: 0;
    width: 86px; height: 230px;
    background: var(--barcode-white);
    border: 1px solid var(--barcode-edge);
  }

  .oil--lavender .oil-band { background: var(--lavender); }
  .oil--frankincense .oil-band { background: var(--frankincense); }
  .oil--cedarwood .oil-band { background: var(--cedarwood); }
  .oil--eucalyptus .oil-band { background: var(--eucalyptus); }
  .oil--lemon .oil-band { background: var(--lemon); }
  .oil--orange .oil-band { background: var(--orange); }
  .oil--peppermint .oil-band { background: var(--peppermint); }
  .oil--rosemary .oil-band { background: var(--rosemary); }
  .oil--tea-tree .oil-band { background: var(--tea-tree); }
</style>
</head>
<body>

<!-- Featured label -->
<section class="label oil--lavender" style="left:375px; top:40px;">
  <div class="label__art" role="img" aria-label="Faint line drawing of lavender sprigs"></div>
  <div class="caution"><span class="caution__title">CAUTION:</span><span class="caution__head">EYE AND SKIN IRRITANT</span>Avoid contact with eyes and<br>skin. Wash hands after<br>handling.<br>If eye contact occurs, flush<br>with water for 15 minutes.<br>Not intended for topical or<br>internal use.<br>Contains Essential Oils.<span class="caution__ingredients">Ingredients: 100% Pure Essential Oil, GC Tested</span><span class="caution__keep">KEEP OUT OF REACH OF CHILDREN</span></div>
  <div class="brand"><span class="brand__mark"></span><div class="brand__name">SOLENNE</div><div class="brand__claim">100% Pure<br>Essential Oil</div><div class="brand__tested">GC TESTED</div><div class="brand__volume">0.33 fl oz (10 ml)</div></div>
  <div class="oil-band"><span class="oil-band__name">Lavender</span></div>
  <div class="info"><div class="info__turn"><div class="info__social">visit us @solenne</div><div class="info__address">PRODUCED BY: SOLENNE, ADDRESS<br>CITY, STATE, COUNTRY, CODE</div></div></div>
  <div class="barcode-space"></div>
</section>

<!-- Left column -->
<section class="label label--small oil--frankincense" style="left:315px; top:308px;">
  <div class="label__art" role="img" aria-label="Faint drawing of frankincense resin"></div>
  <div class="caution"><span class="caution__title">CAUTION:</span><span class="caution__head">EYE AND SKIN IRRITANT</span>Avoid contact with eyes and<br>skin. Wash hands after<br>handling.<br>If eye contact occurs, flush<br>with water for 15 minutes.<br>Not intended for topical or<br>internal use.<br>Contains Essential Oils.<span class="caution__ingredients">Ingredients: 100% Pure Essential Oil, GC Tested</span><span class="caution__keep">KEEP OUT OF REACH OF CHILDREN</span></div>
  <div class="brand"><span class="brand__mark"></span><div class="brand__name">SOLENNE</div><div class="brand__claim">100% Pure<br>Essential Oil</div><div class="brand__tested">GC TESTED</div><div class="brand__volume">0.33 fl oz (10 ml)</div></div>
  <div class="oil-band"><span class="oil-band__name">Frankincense</span></div>
  <div class="info"><div class="info__turn"><div class="info__social">visit us @solenne</div><div class="info__address">PRODUCED BY: SOLENNE, ADDRESS<br>CITY, STATE, COUNTRY, CODE</div></div></div>
  <div class="barcode-space"></div>
</section>

<section class="label label--small oil--cedarwood" style="left:315px; top:447px;">
  <div class="label__art" role="img" aria-label="Faint drawing of cedar branches"></div>
  <div class="caution"><span class="caution__title">CAUTION:</span><span class="caution__head">EYE AND SKIN IRRITANT</span>Avoid contact with eyes and<br>skin. Wash hands after<br>handling.<br>If eye contact occurs, flush<br>with water for 15 minutes.<br>Not intended for topical or<br>internal use.<br>Contains Essential Oils.<span class="caution__ingredients">Ingredients: 100% Pure Essential Oil, GC Tested</span><span class="caution__keep">KEEP OUT OF REACH OF CHILDREN</span></div>
  <div class="brand"><span class="brand__mark"></span><div class="brand__name">SOLENNE</div><div class="brand__claim">100% Pure<br>Essential Oil</div><div class="brand__tested">GC TESTED</div><div class="brand__volume">0.33 fl oz (10 ml)</div></div>
  <div class="oil-band"><span class="oil-band__name">Cedarwood</span></div>
  <div class="info"><div class="info__turn"><div class="info__social">visit us @solenne</div><div class="info__address">PRODUCED BY: SOLENNE, ADDRESS<br>CITY, STATE, COUNTRY, CODE</div></div></div>
  <div class="barcode-space"></div>
</section>

<section class="label label--small oil--eucalyptus" style="left:315px; top:587px;">
  <div class="label__art" role="img" aria-label="Faint drawing of eucalyptus leaves"></div>
  <div class="caution"><span class="caution__title">CAUTION:</span><span class="caution__head">EYE AND SKIN IRRITANT</span>Avoid contact with eyes and<br>skin. Wash hands after<br>handling.<br>If eye contact occurs, flush<br>with water for 15 minutes.<br>Not intended for topical or<br>internal use.<br>Contains Essential Oils.<span class="caution__ingredients">Ingredients: 100% Pure Essential Oil, GC Tested</span><span class="caution__keep">KEEP OUT OF REACH OF CHILDREN</span></div>
  <div class="brand"><span class="brand__mark"></span><div class="brand__name">SOLENNE</div><div class="brand__claim">100% Pure<br>Essential Oil</div><div class="brand__tested">GC TESTED</div><div class="brand__volume">0.33 fl oz (10 ml)</div></div>
  <div class="oil-band"><span class="oil-band__name">Eucalyptus</span></div>
  <div class="info"><div class="info__turn"><div class="info__social">visit us @solenne</div><div class="info__address">PRODUCED BY: SOLENNE, ADDRESS<br>CITY, STATE, COUNTRY, CODE</div></div></div>
  <div class="barcode-space"></div>
</section>

<section class="label label--small oil--lemon" style="left:315px; top:733px;">
  <div class="label__art" role="img" aria-label="Faint drawing of lemon slices"></div>
  <div class="caution"><span class="caution__title">CAUTION:</span><span class="caution__head">EYE AND SKIN IRRITANT</span>Avoid contact with eyes and<br>skin. Wash hands after<br>handling.<br>If eye contact occurs, flush<br>with water for 15 minutes.<br>Not intended for topical or<br>internal use.<br>Contains Essential Oils.<span class="caution__ingredients">Ingredients: 100% Pure Essential Oil, GC Tested</span><span class="caution__keep">KEEP OUT OF REACH OF CHILDREN</span></div>
  <div class="brand"><span class="brand__mark"></span><div class="brand__name">SOLENNE</div><div class="brand__claim">100% Pure<br>Essential Oil</div><div class="brand__tested">GC TESTED</div><div class="brand__volume">0.33 fl oz (10 ml)</div></div>
  <div class="oil-band"><span class="oil-band__name">Lemon</span></div>
  <div class="info"><div class="info__turn"><div class="info__social">visit us @solenne</div><div class="info__address">PRODUCED BY: SOLENNE, ADDRESS<br>CITY, STATE, COUNTRY, CODE</div></div></div>
  <div class="barcode-space"></div>
</section>

<!-- Right column -->
<section class="label label--small oil--orange" style="left:770px; top:302px;">
  <div class="label__art" role="img" aria-label="Faint drawing of orange slices"></div>
  <div class="caution"><span class="caution__title">CAUTION:</span><span class="caution__head">EYE AND SKIN IRRITANT</span>Avoid contact with eyes and<br>skin. Wash hands after<br>handling.<br>If eye contact occurs, flush<br>with water for 15 minutes.<br>Not intended for topical or<br>internal use.<br>Contains Essential Oils.<span class="caution__ingredients">Ingredients: 100% Pure Essential Oil, GC Tested</span><span class="caution__keep">KEEP OUT OF REACH OF CHILDREN</span></div>
  <div class="brand"><span class="brand__mark"></span><div class="brand__name">SOLENNE</div><div class="brand__claim">100% Pure<br>Essential Oil</div><div class="brand__tested">GC TESTED</div><div class="brand__volume">0.33 fl oz (10 ml)</div></div>
  <div class="oil-band"><span class="oil-band__name">Orange</span></div>
  <div class="info"><div class="info__turn"><div class="info__social">visit us @solenne</div><div class="info__address">PRODUCED BY: SOLENNE, ADDRESS<br>CITY, STATE, COUNTRY, CODE</div></div></div>
  <div class="barcode-space"></div>
</section>

<section class="label label--small oil--peppermint" style="left:770px; top:444px;">
  <div class="label__art" role="img" aria-label="Faint drawing of peppermint leaves"></div>
  <div class="caution"><span class="caution__title">CAUTION:</span><span class="caution__head">EYE AND SKIN IRRITANT</span>Avoid contact with eyes and<br>skin. Wash hands after<br>handling.<br>If eye contact occurs, flush<br>with water for 15 minutes.<br>Not intended for topical or<br>internal use.<br>Contains Essential Oils.<span class="caution__ingredients">Ingredients: 100% Pure Essential Oil, GC Tested</span><span class="caution__keep">KEEP OUT OF REACH OF CHILDREN</span></div>
  <div class="brand"><span class="brand__mark"></span><div class="brand__name">SOLENNE</div><div class="brand__claim">100% Pure<br>Essential Oil</div><div class="brand__tested">GC TESTED</div><div class="brand__volume">0.33 fl oz (10 ml)</div></div>
  <div class="oil-band"><span class="oil-band__name">Peppermint</span></div>
  <div class="info"><div class="info__turn"><div class="info__social">visit us @solenne</div><div class="info__address">PRODUCED BY: SOLENNE, ADDRESS<br>CITY, STATE, COUNTRY, CODE</div></div></div>
  <div class="barcode-space"></div>
</section>

<section class="label label--small oil--rosemary" style="left:770px; top:589px;">
  <div class="label__art" role="img" aria-label="Faint drawing of rosemary sprigs"></div>
  <div class="caution"><span class="caution__title">CAUTION:</span><span class="caution__head">EYE AND SKIN IRRITANT</span>Avoid contact with eyes and<br>skin. Wash hands after<br>handling.<br>If eye contact occurs, flush<br>with water for 15 minutes.<br>Not intended for topical or<br>internal use.<br>Contains Essential Oils.<span class="caution__ingredients">Ingredients: 100% Pure Essential Oil, GC Tested</span><span class="caution__keep">KEEP OUT OF REACH OF CHILDREN</span></div>
  <div class="brand"><span class="brand__mark"></span><div class="brand__name">SOLENNE</div><div class="brand__claim">100% Pure<br>Essential Oil</div><div class="brand__tested">GC TESTED</div><div class="brand__volume">0.33 fl oz (10 ml)</div></div>
  <div class="oil-band"><span class="oil-band__name">Rosemary</span></div>
  <div class="info"><div class="info__turn"><div class="info__social">visit us @solenne</div><div class="info__address">PRODUCED BY: SOLENNE, ADDRESS<br>CITY, STATE, COUNTRY, CODE</div></div></div>
  <div class="barcode-space"></div>
</section>

<section class="label label--small oil--tea-tree" style="left:770px; top:739px;">
  <div class="label__art" role="img" aria-label="Faint drawing of tea tree branches"></div>
  <div class="caution"><span class="caution__title">CAUTION:</span><span class="caution__head">EYE AND SKIN IRRITANT</span>Avoid contact with eyes and<br>skin. Wash hands after<br>handling.<br>If eye contact occurs, flush<br>with water for 15 minutes.<br>Not intended for topical or<br>internal use.<br>Contains Essential Oils.<span class="caution__ingredients">Ingredients: 100% Pure Essential Oil, GC Tested</span><span class="caution__keep">KEEP OUT OF REACH OF CHILDREN</span></div>
  <div class="brand"><span class="brand__mark"></span><div class="brand__name">SOLENNE</div><div class="brand__claim">100% Pure<br>Essential Oil</div><div class="brand__tested">GC TESTED</div><div class="brand__volume">0.33 fl oz (10 ml)</div></div>
  <div class="oil-band"><span class="oil-band__name">Tea Tree</span></div>
  <div class="info"><div class="info__turn"><div class="info__social">visit us @solenne</div><div class="info__address">PRODUCED BY: SOLENNE, ADDRESS<br>CITY, STATE, COUNTRY, CODE</div></div></div>
  <div class="barcode-space"></div>
</section>

</body>
</html>
```